Music Quizz Application

Hello,

I want a new design for my Blind test (music quizz) application on Korvex. You will find attached the images I want to replace. I need something with the same element (menu / song title) but with a different look!

Same, new icon, you have carte blanche to this one.

I am looking for something fresh…. I'm looking for something with a real artistic choice, contrast, colours, etc.

As a marketing screenshot, I want something classic, you'll find an example attached, feel free to innovate.

To sum-up :

- One new view for my App
- One new icon
- One marketing screenshot

screen resolution :
640×960
icon resolution :
1024x1024

Target Market(s)

15-30 years

Industry/Entity Type

Marketing

```html
<!DOCTYPE html>
<html lang="en">
<head>
<meta charset="utf-8">
<title>Earshot – Home</title>
<link rel="stylesheet" href="https://fonts.googleapis.com/css2?family=Ubuntu:wght@300;500&family=Arimo:wght@700&display=swap">
<style>
  :root {
    --bar-bg: #000000;
    --bar-text: #d8d8d8;
    --title-ink: #1c1c1c;
    --menu-top: #3b3835;
    --menu-bottom: #121110;
    --menu-text: #f4f1ec;
    --menu-rule: rgba(255,255,255,0.22);
    --mark-fill: #f3f3f3;
  }
  * { margin: 0; padding: 0; box-sizing: border-box; }
  html, body { width: 800px; height: 1200px; overflow: hidden; background: #000; }
  .screen { position: relative; width: 800px; height: 1200px; overflow: hidden; }

  .backdrop {
    position: absolute; inset: 50px 0 0 0;
    background:
      radial-gradient(ellipse 260px 300px at 400px 560px, #ffffff 0%, rgba(255,255,255,0.85) 45%, rgba(255,255,255,0) 100%),
      radial-gradient(ellipse 220px 260px at 40px 380px, #49c9a6 0%, rgba(73,201,166,0) 100%),
      radial-gradient(ellipse 200px 220px at 230px 220px, #b8c46a 0%, rgba(184,196,106,0) 100%),
      radial-gradient(ellipse 260px 260px at 720px 430px, #f3b63a 0%, rgba(243,182,58,0) 100%),
      radial-gradient(ellipse 200px 200px at 690px 170px, #c8501c 0%, rgba(200,80,28,0) 100%),
      radial-gradient(ellipse 220px 250px at 60px 900px, #7fd7b8 0%, rgba(127,215,184,0) 100%),
      radial-gradient(ellipse 240px 240px at 760px 820px, #e58a3a 0%, rgba(229,138,58,0) 100%),
      radial-gradient(ellipse 160px 140px at 250px 1080px, #2b4a6e 0%, rgba(43,74,110,0) 100%),
      linear-gradient(180deg, #1c1a12 0%, #3a2a14 30%, #4a3a2a 60%, #100d0a 100%);
  }

  .status-bar {
    position: absolute; top: 0; left: 0; width: 800px; height: 50px;
    background: var(--bar-bg); color: var(--bar-text);
    font-family: "Arimo", sans-serif; font-weight: 700; font-size: 28px;
  }
  .status-bar .carrier { position: absolute; left: 10px; top: 8px; display: flex; align-items: center; gap: 10px; }
  .status-bar .signal { display: flex; align-items: flex-end; gap: 3px; height: 22px; }
  .status-bar .signal span { width: 6px; height: 3px; background: #888; }
  .status-bar .signal span:first-child { height: 10px; background: var(--bar-text); }
  .status-bar .network { margin-left: 14px; }
  .status-bar .clock { position: absolute; left: 0; right: 0; top: 8px; text-align: center; }
  .status-bar .power { position: absolute; right: 12px; top: 8px; display: flex; align-items: center; gap: 12px; }

  .brand { position: absolute; left: 0; width: 800px; text-align: center; }
  .brand-dot {
    position: absolute; left: 262px; top: 218px; width: 276px; height: 276px;
    border-radius: 50%; background: var(--mark-fill);
    box-shadow: 0 4px 14px rgba(0,0,0,0.15);
  }
  .brand-name {
    top: 520px;
    font-family: "Ubuntu", sans-serif; font-weight: 300; font-size: 118px;
    color: var(--title-ink); letter-spacing: 1px; line-height: 1.1;
  }

  .main-menu {
    position: absolute; left: 157px; top: 737px; width: 487px; height: 275px;
    background: linear-gradient(180deg, var(--menu-top) 0%, #221f1c 55%, var(--menu-bottom) 100%);
    border: 1px solid rgba(0,0,0,0.6); border-radius: 5px;
    box-shadow: 0 2px 8px rgba(0,0,0,0.45), inset 0 1px 0 rgba(255,255,255,0.15);
    list-style: none;
    font-family: "Ubuntu", sans-serif; font-weight: 500; font-size: 24px; color: var(--menu-text);
  }
  .main-menu li { position: absolute; left: 0; width: 100%; text-align: center; }
  .main-menu .item-quick { top: 40px; }
  .main-menu .item-blind { top: 130px; }
  .main-menu .item-challenge { top: 214px; }
  .menu-rule { position: absolute; left: 62px; width: 363px; height: 1px; background: var(--menu-rule); }
  .menu-rule.first { top: 97px; }
  .menu-rule.second { top: 181px; }
</style>
</head>
<body>
<div class="screen">
  <div class="backdrop" role="img" aria-label="Blurred colourful bokeh background in green, amber and orange tones"></div>

  <header class="status-bar">
    <div class="carrier">
      <div class="signal"><span></span><span></span><span></span><span></span><span></span></div>
      <span>NOVA</span><span class="network">3G</span>
    </div>
    <div class="clock">12:14</div>
    <div class="power">
      <svg width="18" height="30" viewBox="0 0 18 30" aria-label="Bluetooth">
        <polyline points="3,8 15,21 9,27 9,3 15,9 3,22" fill="none" stroke="#777" stroke-width="2.5"/>
      </svg>
      <span>89 %</span>
      <svg width="44" height="24" viewBox="0 0 44 24" aria-label="Battery charging">
        <rect x="1.5" y="2.5" width="36" height="19" rx="2" fill="none" stroke="#d8d8d8" stroke-width="2.5"/>
        <rect x="39" y="8" width="4" height="8" fill="#d8d8d8"/>
        <rect x="5" y="6" width="29" height="12" fill="#d8d8d8"/>
        <polygon points="22,4 14,13 20,13 16,21 26,11 20,11" fill="#000"/>
      </svg>
    </div>
  </header>

  <div class="brand-dot"></div>
  <h1 class="brand brand-name">Earshot</h1>

  <ul class="main-menu">
    <li class="item-quick">Quick Game</li>
    <div class="menu-rule first"></div>
    <li class="item-blind">Blind Test</li>
    <div class="menu-rule second"></div>
    <li class="item-challenge">Challenge</li>
  </ul>
</div>
</body>
</html>
```